Website for software company "velora"

We need a website for our software company/startup named "velora". We are developing several products (currently 3 standard-software products) which are all in different sectors, but all our products are available for Laptops/PC/Mobile Phones/Tablets, ... We do also create custom software and support our customers with consulting to optimize their processes.
We already have a Logo which you can find in the attached files.
We are a young team of 4 members (two founders and 2 employees).

To get an idea of our products -> the first one is a planning software for healthcare organizations (eg. BlueHaven, firebrigade, pharmacy), the second one is a booking software for sport clubs and the third one is a competition software for sports hunting. You see very diverse. Include or ignore this info of our products as you like.

The design has to be a bootstrap 4 (or higher) design. We have licenced FontAwesome as iconset. Responsive design should come without saying.

• Starting page, product pages, news section, contact, team, services

```html
<!DOCTYPE html>
<html lang="en">
<head>
<meta charset="utf-8">
<title>velora – Software for every sector</title>
<link rel="stylesheet" href="https://fonts.googleapis.com/css2?family=Outfit:wght@300;400;500;600;700&display=swap">
<style>
:root{
  --orange:#f47b20;
  --orange-soft:#f7a25f;
  --navy:#212b38;
  --navy-deep:#18212c;
  --ink:#2a2f37;
  --muted:#5b6068;
  --field:#3a4656;
  --field-line:#55606e;
  --white:#ffffff;
}
*{margin:0;padding:0;box-sizing:border-box}
html,body{width:1200px;height:4254px;overflow:hidden}
body{position:relative;font-family:"Outfit",sans-serif;color:var(--ink);background:var(--white)}
.abs{position:absolute}
a{color:inherit;text-decoration:none}
.btn{position:absolute;display:flex;align-items:center;justify-content:center;gap:10px;background:var(--orange);color:var(--white);font-weight:600;border-radius:40px}
.btn svg{width:20px;height:20px}
.btn-sm{font-size:14px;gap:7px}
.btn-sm svg{width:15px;height:15px}

/* header */
.site-header{position:absolute;left:0;top:0;width:1200px;height:74px}
.brand{position:absolute;display:flex;align-items:center;gap:10px;font-weight:700;color:var(--ink);letter-spacing:1px}
.brand .mark{width:14px;height:14px;background:var(--orange)}
.main-nav{position:absolute;left:398px;top:24px;display:flex;gap:0}
.main-nav a{font-size:14px;color:var(--ink);margin-right:0}
.main-nav a.active{color:var(--orange)}
.phone-btn{left:848px;top:16px;width:177px;height:42px;font-size:17px;gap:8px;justify-content:flex-start;padding-left:6px}
.phone-btn .ring{width:32px;height:32px;border-radius:50%;background:var(--white);display:flex;align-items:center;justify-content:center}
.phone-btn .ring svg{width:17px;height:17px}

/* decorative section bands */
.band{position:absolute;left:0;width:1200px}
.band svg{position:absolute;left:0;top:0;width:1200px;height:100%}

.section-title{position:absolute;left:0;width:1200px;text-align:center;font-size:40px;font-weight:600;line-height:1}
.section-title .accent{color:var(--orange);font-weight:500}
.title-bar{position:absolute;left:589px;width:22px;height:6px;background:var(--orange)}

/* hero */
.hero-title{left:173px;top:215px;font-size:48px;font-weight:700;line-height:54px;color:var(--white)}
.hero-sub{left:173px;top:336px;font-size:20px;color:var(--white)}

/* welcome */
.welcome-kicker{left:183px;top:692px;font-size:33px;font-weight:500;color:var(--ink);display:flex;align-items:center;gap:10px}
.welcome-kicker .mark{width:16px;height:16px;background:var(--orange)}
.welcome-name{left:183px;top:730px;font-size:58px;font-weight:600;letter-spacing:2px;color:var(--ink)}
.welcome-text{left:459px;top:665px;width:575px;font-size:20.5px;line-height:31px;color:var(--muted);font-weight:300}

/* products */
.product-card{position:absolute;top:1162px;width:260px;height:387px;border:3px solid var(--orange);border-radius:130px}
.product-inner{position:absolute;left:10px;top:10px;right:10px;bottom:10px;background:var(--white);border-radius:120px;overflow:hidden}
.product-cap{position:absolute;left:0;top:0;width:100%;height:148px;background:var(--orange);border-radius:0 0 50% 50% / 0 0 70px 70px;border-bottom:4px solid var(--white);box-shadow:0 3px 0 var(--orange)}
.product-icon{position:absolute;left:84px;top:46px;width:68px;height:68px;border-radius:50%;border:3px solid var(--white);opacity:.9}
.product-name{position:absolute;left:0;top:160px;width:100%;text-align:center;font-size:21px;font-weight:600;line-height:23px;color:var(--ink)}
.product-text{position:absolute;left:18px;right:18px;top:212px;text-align:center;font-size:17px;line-height:25px;color:var(--muted);font-weight:300}
.product-link{position:absolute;left:0;top:310px;width:100%;display:flex;justify-content:center;align-items:center;gap:7px;font-size:17px;font-weight:600;color:var(--orange)}
.product-link svg{width:16px;height:16px}

/* services */
.service-card{position:absolute;top:1809px;width:268px;height:362px;background:var(--white);box-shadow:0 4px 18px rgba(0,0,0,.12)}
.service-photo{position:absolute;left:0;top:0;width:268px;height:174px}
.card-title{position:absolute;left:20px;font-size:20px;font-weight:600;color:var(--ink)}
.card-text{position:absolute;left:20px;width:235px;font-size:14.5px;line-height:21.5px;color:var(--muted);font-weight:300}
.service-card .btn{left:20px;top:306px;width:128px;height:38px}

/* team */
.member{position:absolute;top:2414px;width:200px;text-align:center;color:var(--white)}
.member svg{display:block;margin:0 auto;width:200px;height:200px}
.member-name{margin-top:14px;font-size:17px;font-weight:600}
.member-role{font-size:13px;font-style:italic;color:#8f98a4;font-weight:300}

/* news */
.news-card{position:absolute;top:2937px;width:268px}
.news-photo{position:absolute;left:0;top:0;width:268px;height:185px}
.news-date{position:absolute;left:12px;top:172px;padding:0 10px;height:24px;line-height:24px;background:var(--orange);color:var(--white);font-size:13px;font-weight:500}
.news-card .card-title{left:0;top:208px}
.news-card .card-text{left:0;top:242px;width:268px}
.news-card .btn{left:0;top:315px;width:128px;height:37px}
.slider-arrow{position:absolute;top:3006px;width:49px;height:47px;display:flex;align-items:center;justify-content:center}
.slider-arrow svg{width:18px;height:18px}

/* contact */
.field{position:absolute;background:var(--field);border:1px solid var(--field-line);color:var(--white);font-size:15px;padding:10px 12px;font-weight:300}

/* footer */
.footer-head{position:absolute;top:3982px;font-size:14px;font-weight:600;color:var(--orange);letter-spacing:.3px}
.footer-list{position:absolute;list-style:none;font-size:14px;color:var(--ink);font-weight:300}
.footer-list li{position:relative;padding-left:16px;line-height:19px}
.footer-list li::before{content:"";position:absolute;left:0;top:5px;border-left:6px solid var(--orange);border-top:4px solid transparent;border-bottom:4px solid transparent}
.social{position:absolute;top:4080px;width:36px;height:36px;border-radius:50%;background:#d9dadc}
.copyright{position:absolute;left:190px;top:4167px;font-size:13px;color:var(--muted);font-weight:300}
.copyright span{color:var(--orange)}
.contact-row{position:absolute;left:820px;display:flex;gap:12px;font-size:14px;line-height:22px;color:var(--ink);font-weight:300}
.contact-row svg{width:14px;height:14px;flex:none;margin-top:4px}
</style>
</head>
<body>

<svg width="0" height="0" style="position:absolute">
  <symbol id="go" viewBox="0 0 20 20"><circle cx="10" cy="10" r="9.5" fill="#fff"/><path d="M5 10h8M10 6l4 4-4 4" stroke="#f47b20" stroke-width="2.2" fill="none" stroke-linecap="round" stroke-linejoin="round"/></symbol>
  <symbol id="go-orange" viewBox="0 0 20 20"><circle cx="10" cy="10" r="9.5" fill="#f47b20"/><path d="M5 10h8M10 6l4 4-4 4" stroke="#fff" stroke-width="2.2" fill="none" stroke-linecap="round" stroke-linejoin="round"/></symbol>
  <symbol id="phone" viewBox="0 0 24 24"><path d="M6.6 10.8a15 15 0 006.6 6.6l2.2-2.2c.3-.3.7-.4 1-.2 1.1.4 2.3.6 3.6.6.6 0 1 .4 1 1V20c0 .6-.4 1-1 1A17 17 0 013 4c0-.6.4-1 1-1h3.5c.6 0 1 .4 1 1 0 1.3.2 2.5.6 3.6.1.3 0 .7-.2 1z" fill="currentColor"/></symbol>
</svg>

<!-- header -->
<header class="site-header">
  <div class="brand" style="left:170px;top:22px;font-size:40px"><span class="mark"></span>velora</div>
  <nav class="main-nav">
    <a class="active" href="#" style="position:absolute;left:0">Home</a>
    <a href="#" style="position:absolute;left:70px">Product</a>
    <a href="#" style="position:absolute;left:155px">News</a>
    <a href="#" style="position:absolute;left:222px">Team</a>
    <a href="#" style="position:absolute;left:289px">Services</a>
    <a href="#" style="position:absolute;left:376px">Contact</a>
  </nav>
  <a class="btn phone-btn" href="#"><span class="ring"><svg style="color:var(--orange)"><use href="#phone"/></svg></span>01 555 204 318</a>
</header>

<!-- hero -->
<section class="band" style="top:74px;height:516px">
  <svg viewBox="0 0 1200 516" preserveAspectRatio="none">
    <defs><linearGradient id="heroGrad" x1="0" y1="0" x2="1" y2="1"><stop offset="0" stop-color="#3d4651"/><stop offset=".55" stop-color="#2b333d"/><stop offset="1" stop-color="#4a525c"/></linearGradient></defs>
    <polygon role="img" aria-label="Photo of a businessman working at a computer in an office" points="0,46 360,46 405,0 1200,0 1200,480 510,480 455,516 0,516" fill="url(#heroGrad)"/>
    <polyline points="0,56 365,56 410,12 1200,12" stroke="#f47b20" stroke-width="3" fill="none"/>
    <polyline points="1200,456 500,456 450,500 0,500" stroke="#f47b20" stroke-width="3" fill="none"/>
  </svg>
</section>
<h1 class="abs hero-title">We are Developing<br>Several Products</h1>
<p class="abs hero-sub">Which are all in different sectors</p>
<a class="btn" href="#" style="left:173px;top:376px;width:179px;height:52px;font-size:17px">Know More <svg><use href="#go"/></svg></a>

<!-- welcome -->
<div class="abs welcome-kicker">Welcome to <span class="mark"></span></div>
<div class="abs welcome-name">VELORA</div>
<p class="abs welcome-text">Lorem ipsum dolor sit amet, consectetur adipiscing elit, sed do eiusmod tempor incididunt ut labore et dolore magna aliqua. Quis ipsum suspendisse ultes graa. Risus commodo viverra maecenas accumsan lacus vel facilisis.</p>
<a class="btn" href="#" style="left:459px;top:811px;width:178px;height:52px;font-size:17px">Read More <svg><use href="#go"/></svg></a>

<!-- products -->
<section class="band" style="top:987px;height:672px">
  <svg viewBox="0 0 1200 672" preserveAspectRatio="none">
    <polygon points="0,53 360,53 405,0 1200,0 1200,614 510,614 455,672 0,672" fill="#212b38"/>
    <polyline points="0,64 365,64 415,14 1200,14" stroke="#f47b20" stroke-width="3" fill="none"/>
    <polyline points="1200,602 500,602 450,658 0,658" stroke="#f47b20" stroke-width="3" fill="none"/>
  </svg>
</section>
<h2 class="section-title" style="top:1063px;color:var(--white)"><span class="accent">Our</span> Product</h2>
<div class="title-bar" style="top:1112px"></div>

<article class="product-card" style="left:173px">
  <div class="product-inner">
    <div class="product-cap"><div class="product-icon" role="img" aria-label="Healthcare planning icon"></div></div>
    <h3 class="product-name">Healthcare<br>Organizations</h3>
    <p class="product-text">Risus commodo viverra maecenas accumsan lacus vel facilisis.</p>
    <a class="product-link" href="#">View Details <svg><use href="#go-orange"/></svg></a>
  </div>
</article>
<article class="product-card" style="left:471px">
  <div class="product-inner">
    <div class="product-cap"><div class="product-icon" role="img" aria-label="Booking software icon"></div></div>
    <h3 class="product-name">Booking software<br>For sport clubs</h3>
    <p class="product-text">Risus commodo viverra maecenas accumsan lacus vel facilisis.</p>
    <a class="product-link" href="#">View Details <svg><use href="#go-orange"/></svg></a>
  </div>
</article>
<article class="product-card" style="left:768px">
  <div class="product-inner">
    <div class="product-cap"><div class="product-icon" role="img" aria-label="Competition software icon"></div></div>
    <h3 class="product-name">Competition Software<br>For sports hunting</h3>
    <p class="product-text">Risus commodo viverra maecenas accumsan lacus vel facilisis.</p>
    <a class="product-link" href="#">View Details <svg><use href="#go-orange"/></svg></a>
  </div>
</article>

<!-- services -->
<h2 class="section-title" style="top:1726px"><span class="accent">Our</span> Services</h2>
<div class="title-bar" style="top:1775px"></div>

<article class="service-card" style="left:173px">
  <div class="service-photo" role="img" aria-label="Photo of hands typing on a laptop keyboard" style="background:linear-gradient(135deg,#9fb1c2,#5d6b78 60%,#c9ced3)"></div>
  <h3 class="card-title" style="top:196px">Vestibulum viverra</h3>
  <p class="card-text" style="top:230px">Vivamus et velit a odio semper blandit eu eget odio. Duis non bibendum urna. Morbi lacinia,</p>
  <a class="btn btn-sm" href="#">Read More <svg><use href="#go"/></svg></a>
</article>
<article class="service-card" style="left:467px">
  <div class="service-photo" role="img" aria-label="Photo of a developer coding at a desktop computer" style="background:linear-gradient(135deg,#e4e2dc,#8d8c86 55%,#4b5560)"></div>
  <h3 class="card-title" style="top:196px">Vestibulum viverra</h3>
  <p class="card-text" style="top:230px">Vivamus et velit a odio semper blandit eu eget odio. Duis non bibendum urna. Morbi lacinia,</p>
  <a class="btn btn-sm" href="#">Read More <svg><use href="#go"/></svg></a>
</article>
<article class="service-card" style="left:760px">
  <div class="service-photo" role="img" aria-label="Photo of a consultant smiling at his desk" style="background:linear-gradient(135deg,#d9d3b8,#8fa6c9 60%,#e9e6dc)"></div>
  <h3 class="card-title" style="top:196px">Vestibulum viverra</h3>
  <p class="card-text" style="top:230px">Vivamus et velit a odio semper blandit eu eget odio. Duis non bibendum urna. Morbi lacinia,</p>
  <a class="btn btn-sm" href="#">Read More <svg><use href="#go"/></svg></a>
</article>

<!-- team -->
<section class="band" style="top:2240px;height:555px">
  <svg viewBox="0 0 1200 555" preserveAspectRatio="none">
    <defs><linearGradient id="teamGrad" x1="0" y1="0" x2="1" y2="1"><stop offset="0" stop-color="#1c2a3c"/><stop offset=".5" stop-color="#17202b"/><stop offset="1" stop-color="#26313e"/></linearGradient></defs>
    <polygon role="img" aria-label="Dark photo of an office workspace" points="0,53 360,53 405,0 1200,0 1200,497 510,497 455,555 0,555" fill="url(#teamGrad)"/>
    <polyline points="0,64 365,64 415,14 1200,14" stroke="#f47b20" stroke-width="3" fill="none"/>
    <polyline points="1200,485 500,485 450,541 0,541" stroke="#f47b20" stroke-width="3" fill="none"/>
  </svg>
</section>
<h2 class="section-title" style="top:2326px;color:var(--white)"><span class="accent">Our</span> Team Mamber</h2>
<div class="title-bar" style="top:2375px"></div>

<div class="member" style="left:172px">
  <svg viewBox="0 0 200 200"><circle cx="100" cy="100" r="95" fill="none" stroke="#f47b20" stroke-width="10" stroke-dasharray="2 4"/><circle cx="100" cy="100" r="81" fill="none" stroke="#f47b20" stroke-width="2"/><circle role="img" aria-label="Portrait of a founder" cx="100" cy="100" r="78" fill="#d7d9dc"/></svg>
  <div class="member-name">Lorem ipsum</div><div class="member-role">Founders</div>
</div>
<div class="member" style="left:390px">
  <svg viewBox="0 0 200 200"><circle cx="100" cy="100" r="95" fill="none" stroke="#f47b20" stroke-width="10" stroke-dasharray="2 4"/><circle cx="100" cy="100" r="81" fill="none" stroke="#f47b20" stroke-width="2"/><circle role="img" aria-label="Portrait of a founder" cx="100" cy="100" r="78" fill="#e2dcd6"/></svg>
  <div class="member-name">Lorem ipsum</div><div class="member-role">Founders</div>
</div>
<div class="member" style="left:608px">
  <svg viewBox="0 0 200 200"><circle cx="100" cy="100" r="95" fill="none" stroke="#f47b20" stroke-width="10" stroke-dasharray="2 4"/><circle cx="100" cy="100" r="81" fill="none" stroke="#f47b20" stroke-width="2"/><circle role="img" aria-label="Portrait of an employee" cx="100" cy="100" r="78" fill="#cfd5dd"/></svg>
  <div class="member-name">Lorem ipsum</div><div class="member-role">Employee</div>
</div>
<div class="member" style="left:826px">
  <svg viewBox="0 0 200 200"><circle cx="100" cy="100" r="95" fill="none" stroke="#f47b20" stroke-width="10" stroke-dasharray="2 4"/><circle cx="100" cy="100" r="81" fill="none" stroke="#f47b20" stroke-width="2"/><circle role="img" aria-label="Portrait of an employee" cx="100" cy="100" r="78" fill="#e6e6e6"/></svg>
  <div class="member-name">Lorem ipsum</div><div class="member-role">Employee</div>
</div>

<!-- news -->
<h2 class="section-title" style="top:2850px"><span class="accent">Latest</span> News</h2>
<div class="title-bar" style="top:2899px"></div>

<article class="news-card" style="left:173px">
  <div class="news-photo" role="img" aria-label="Photo of a man working on a laptop by a window" style="background:linear-gradient(135deg,#b7c6d3,#6f8396 55%,#d7dde2)"></div>
  <span class="news-date">April 16, 2022</span>
  <h3 class="card-title">Vivamus et velit a odio</h3>
  <p class="card-text">Donec cursus dapibus fermentum. Proin auctor diam maximus, hendrerit libero sit amet, porta nulla.</p>
  <a class="btn btn-sm" href="#">Read More <svg><use href="#go"/></svg></a>
</article>
<article class="news-card" style="left:467px">
  <div class="news-photo" role="img" aria-label="Photo of a hand holding a smartphone showing a download screen" style="background:linear-gradient(135deg,#8a7a62,#4c5a4f 50%,#3fae7e 70%,#b8a88c)"></div>
  <span class="news-date">April 16, 2022</span>
  <h3 class="card-title">Vivamus et velit a odio</h3>
  <p class="card-text">Donec cursus dapibus fermentum. Proin auctor diam maximus, hendrerit libero sit amet, porta nulla.</p>
  <a class="btn btn-sm" href="#">Read More <svg><use href="#go"/></svg></a>
</article>
<article class="news-card" style="left:760px">
  <div class="news-photo" role="img" aria-label="Photo of a cheerful man holding a tablet" style="background:linear-gradient(135deg,#eceae8,#f2c9c4 55%,#e3e1df)"></div>
  <span class="news-date">April 16, 2022</span>
  <h3 class="card-title">Vivamus et velit a odio</h3>
  <p class="card-text">Donec cursus dapibus fermentum. Proin auctor diam maximus, hendrerit libero sit amet, porta nulla.</p>
  <a class="btn btn-sm" href="#">Read More <svg><use href="#go"/></svg></a>
</article>
<a class="slider-arrow" href="#" aria-label="Previous" style="left:149px;background:#4a4f56"><svg viewBox="0 0 18 18"><path d="M12 2L5 9l7 7" stroke="#fff" stroke-width="1.6" fill="none"/></svg></a>
<a class="slider-arrow" href="#" aria-label="Next" style="left:1008px;background:var(--orange-soft)"><svg viewBox="0 0 18 18"><path d="M6 2l7 7-7 7" stroke="#fff" stroke-width="1.6" fill="none"/></svg></a>

<!-- contact -->
<section class="band" style="top:3376px;height:562px">
  <svg viewBox="0 0 1200 562" preserveAspectRatio="none">
    <defs><linearGradient id="contactGrad" x1="0" y1="0" x2="1" y2="1"><stop offset="0" stop-color="#1f2835"/><stop offset=".5" stop-color="#1a222d"/><stop offset="1" stop-color="#2a333f"/></linearGradient></defs>
    <polygon role="img" aria-label="Dark photo of a person at a desk" points="0,53 360,53 405,0 1200,0 1200,504 510,504 455,562 0,562" fill="url(#contactGrad)"/>
    <polyline points="0,64 365,64 415,14 1200,14" stroke="#f47b20" stroke-width="3" fill="none"/>
    <polyline points="1200,492 500,492 450,548 0,548" stroke="#f47b20" stroke-width="3" fill="none"/>
  </svg>
</section>
<h2 class="section-title" style="top:3472px;color:var(--white)"><span class="accent">Get In</span> Touch</h2>
<div class="title-bar" style="top:3521px"></div>
<form>
  <div class="field" style="left:236px;top:3561px;width:236px;height:36px;padding-top:8px">Full Name</div>
  <div class="field" style="left:480px;top:3561px;width:238px;height:36px;padding-top:8px">Email</div>
  <div class="field" style="left:726px;top:3561px;width:240px;height:36px;padding-top:8px">Phone</div>
  <div class="field" style="left:236px;top:3609px;width:730px;height:127px">Your Message</div>
  <a class="btn" href="#" style="left:523px;top:3759px;width:152px;height:45px;font-size:17px">Submit <svg><use href="#go"/></svg></a>
</form>

<!-- footer -->
<footer>
  <div class="brand" style="left:170px;top:4003px;font-size:46px"><span class="mark" style="width:16px;height:16px"></span>velora</div>
  <span class="social" style="left:195px" aria-label="Social profile"></span>
  <span class="social" style="left:241px" aria-label="Social profile"></span>
  <span class="social" style="left:287px" aria-label="Social profile"></span>
  <span class="social" style="left:334px" aria-label="Social profile"></span>
  <p class="copyright">© 2022 <span>velora</span>. All right reserved</p>

  <h4 class="footer-head" style="left:429px">QUCIK LINKS</h4>
  <ul class="footer-list" style="left:429px;top:4015px">
    <li style="margin-bottom:15px">Home</li>
    <li style="margin-bottom:15px">Product</li>
    <li style="margin-bottom:15px">News</li>
    <li style="margin-bottom:15px">Team</li>
    <li style="margin-bottom:15px">Services</li>
    <li>Contact</li>
  </ul>

  <h4 class="footer-head" style="left:568px">PRODUCT</h4>
  <ul class="footer-list" style="left:568px;top:4015px;width:215px">
    <li style="margin-bottom:15px">Healthcare Organizations</li>
    <li style="margin-bottom:15px">Booking software For sport clubs</li>
    <li>Competition Software For sports hunting</li>
  </ul>

  <h4 class="footer-head" style="left:820px">CONTACT INFO</h4>
  <div class="contact-row" style="top:4012px;width:220px"><svg viewBox="0 0 14 14"><path d="M7 0a5 5 0 00-5 5c0 3.6 5 9 5 9s5-5.4 5-9a5 5 0 00-5-5zm0 7a2 2 0 110-4 2 2 0 010 4z" fill="#f47b20"/></svg><span>12 Harbour Lane, over 2000 Sydney, Australia</span></div>
  <div class="contact-row" style="top:4068px"><svg style="color:var(--orange)"><use href="#phone"/></svg><span>01 5550 2043 18</span></div>
  <div class="contact-row" style="top:4102px"><svg viewBox="0 0 14 14"><rect x="0" y="2" width="14" height="10" rx="1" fill="#f47b20"/><path d="M0.5 3l6.5 5 6.5-5" stroke="#fff" stroke-width="1.2" fill="none"/></svg><span>info@velora.at</span></div>
</footer>

</body>
</html>
```